Radio Service company needs ad for trade publication

Airwave Allies provides sales, content, production, technology, and promotion products and services to radio stations to help increase sales and solutions to improve operations and reduce costs. We are looking for a creative ad (sizes 720x250, 300x250, 728x180) with a theme around "MASTER YOUR 2024 BUDGET with AIRWAVE ALLIES". Categories we have products/services to help them get budget into alignment. (1) Sales (2) Content & Programming (3) Technology (4) Production & Imaging (5) Promotions & Marketing (6) Support Services
"Don't go into the new year with an Unrealistic Budget.....We can Help!"

```html
<!DOCTYPE html>
<html lang="en">
<head>
<meta charset="utf-8">
<title>Master Your 2024 Budget with Airwave Allies – Ad Set</title>
<link rel="stylesheet" href="https://fonts.googleapis.com/css2?family=Anton&family=Poppins:wght@500;600;700;800&display=swap">
<style>
  :root{
    --canvas:#1d9bf0;
    --navy-deep:#1c3690;
    --navy:#2547a8;
    --navy-light:#2f57bd;
    --sky:#2aa8f4;
    --white:#ffffff;
    --orange:#f7941d;
    --green:#22a64a;
    --logo-ink:#1f86e0;
  }
  *{box-sizing:border-box;margin:0;padding:0}
  html,body{width:1200px;height:1200px;overflow:hidden;background:var(--canvas)}
  .canvas{position:relative;width:1200px;height:1200px;background:var(--canvas);font-family:"Poppins",sans-serif}

  .ad{position:absolute;overflow:hidden;color:var(--white);box-shadow:0 4px 10px rgba(0,0,0,.35)}
  .ad-backdrop{position:absolute;inset:0;
      background:
        radial-gradient(ellipse at 70% 40%, rgba(90,130,230,.35), transparent 60%),
        linear-gradient(135deg,var(--navy-deep) 0%,var(--navy) 55%,var(--navy-light) 100%)}

  .ad--leaderboard{left:55px;top:30px;width:1092px;height:372px}
  .ad--wide{left:55px;top:445px;width:1092px;height:268px}
  .ad--square{left:55px;top:755px;width:503px;height:423px}

  /* headline: stacked lines, badge on its own row so nothing overlaps */
  .headline{position:absolute;display:flex;flex-direction:column;align-items:flex-start;
      font-family:"Anton",sans-serif;font-weight:400;text-transform:uppercase}
  .headline .hl-line{display:block;white-space:nowrap;line-height:.9}
  .headline .hl-with{display:block;background:var(--sky);color:var(--navy-deep);
      font-family:"Poppins",sans-serif;font-weight:800;line-height:1;text-transform:uppercase}

  .ad--leaderboard .headline{left:27px;top:34px}
  .ad--leaderboard .hl-build{font-size:85px}
  .ad--leaderboard .hl-budget{font-size:32px;margin-top:6px}
  .ad--leaderboard .hl-with{font-size:11px;padding:2px 7px;margin:4px 0 4px 112px}
  .ad--leaderboard .hl-name{font-size:88px}
  .ad--leaderboard .hl-name-2{font-size:51px;margin-top:6px}

  .ad--wide .headline{left:50px;top:12px}
  .ad--wide .hl-build{font-size:75px}
  .ad--wide .hl-budget{font-size:24px;margin-top:3px}
  .ad--wide .hl-with{font-size:9px;padding:2px 6px;margin:2px 0 2px 80px}
  .ad--wide .hl-name{font-size:68px}
  .ad--wide .hl-name-2{font-size:38px;margin-top:3px}

  .ad--square .headline{left:20px;top:14px}
  .ad--square .hl-build{font-size:85px}
  .ad--square .hl-budget{font-size:30px;margin-top:4px}
  .ad--square .hl-with{font-size:10px;padding:2px 7px;margin:3px 0 3px 104px}
  .ad--square .hl-name{font-size:84px}
  .ad--square .hl-name-2{font-size:41px;margin-top:4px}

  .divider{position:absolute;background:rgba(255,255,255,.85)}
  .ad--leaderboard .divider{left:347px;top:60px;width:2px;height:248px}
  .ad--wide .divider{left:287px;top:40px;width:2px;height:160px}
  .ad--square .divider{left:20px;top:270px;width:262px;height:2px}

  /* solutions list */
  .solutions-title{position:absolute;font-weight:700;text-transform:uppercase;white-space:nowrap}
  .solutions{position:absolute;list-style:none}
  .solutions li{position:relative;font-weight:500;line-height:1.3}
  .solutions li::before{content:"";position:absolute;left:-1.05em;top:.22em;
      border-left:.6em solid var(--sky);border-top:.42em solid transparent;border-bottom:.42em solid transparent}

  .ad--leaderboard .solutions-title{left:370px;top:26px;font-size:26px}
  .ad--leaderboard .solutions{left:396px;top:66px;font-size:30px;width:440px}
  .ad--leaderboard .solutions li{margin-bottom:6px}

  .ad--wide .solutions-title{left:309px;top:26px;font-size:26px}
  .ad--wide .solutions{left:335px;top:70px;font-size:30px}
  .ad--wide .solutions li{margin-bottom:4px}

  .ad--square .solutions-title{left:23px;top:281px;font-size:24px}
  .ad--square .solutions{left:50px;top:319px;font-size:22px}
  .ad--square .solutions li{margin-bottom:5px}

  /* brand corner */
  .brand-corner{position:absolute;top:0;right:0}
  .brand-corner svg{position:absolute;inset:0;width:100%;height:100%}
  .brand-name{position:absolute;text-align:center;font-weight:800;color:var(--logo-ink);
      line-height:1.02;text-transform:uppercase}
  .ad--leaderboard .brand-corner{width:262px;height:120px}
  .ad--leaderboard .brand-name{font-size:26px;right:22px;top:26px}
  .ad--wide .brand-corner{width:217px;height:125px}
  .ad--wide .brand-name{font-size:24px;right:18px;top:24px}
  .ad--square .brand-corner{width:221px;height:118px}
  .ad--square .brand-name{font-size:24px;right:18px;top:24px}

  /* growth chart */
  .growth-chart{position:absolute}
  .ad--leaderboard .growth-chart{left:819px;top:100px;width:200px;height:210px}
  .ad--wide .growth-chart{left:932px;top:88px;width:132px;height:138px}
  .ad--square .growth-chart{left:312px;top:100px;width:166px;height:132px}

  /* call-to-action band */
  .cta-band{position:absolute;left:0;right:0;bottom:0;background:var(--orange);
      display:flex;align-items:center;justify-content:center;
      font-weight:700;text-transform:uppercase;white-space:nowrap}
  .ad--leaderboard .cta-band{height:41px;font-size:18.5px}
  .ad--wide .cta-band{height:37px;font-size:18.5px}
</style>
</head>
<body>
<main class="canvas">

  <section class="ad ad--leaderboard" aria-label="Airwave Allies leaderboard ad">
    <div class="ad-backdrop" role="img" aria-label="Deep blue background with faint stock-market candlestick chart"></div>
    <h1 class="headline">
      <span class="hl-line hl-build">Build</span>
      <span class="hl-line hl-budget">Your 2024 Budget</span>
      <span class="hl-with">with</span>
      <span class="hl-line hl-name">Airwave</span>
      <span class="hl-line hl-name-2">Allies</span>
    </h1>
    <div class="divider"></div>
    <h2 class="solutions-title">Solutions for Broadcasters</h2>
    <ul class="solutions">
      <li>Need to Improve Your<br>Cash Flow?</li>
      <li>Need to Streamline Your<br>Expenses?</li>
      <li>Need more Non-Traditional<br>Revenue?</li>
    </ul>
    <div class="brand-corner">
      <svg viewBox="0 0 100 100" preserveAspectRatio="none" aria-hidden="true"><path d="M0 0H100V100C55 100 12 72 0 0Z" fill="#fff"/></svg>
      <p class="brand-name">Airwave<br>Allies</p>
    </div>
    <svg class="growth-chart" viewBox="0 0 130 140" aria-label="Rising bar chart with upward arrow">
      <defs>
        <linearGradient id="bar-fill-a" x1="0" y1="0" x2="0" y2="1"><stop offset="0" stop-color="#35b4ff"/><stop offset="1" stop-color="#1a8ae0"/></linearGradient>
      </defs>
      <rect x="2" y="100" width="20" height="38" fill="url(#bar-fill-a)"/>
      <rect x="28" y="86" width="20" height="52" fill="url(#bar-fill-a)"/>
      <rect x="54" y="72" width="20" height="66" fill="url(#bar-fill-a)"/>
      <rect x="80" y="56" width="20" height="82" fill="url(#bar-fill-a)"/>
      <rect x="106" y="40" width="20" height="98" fill="url(#bar-fill-a)"/>
      <polyline points="4,80 34,56 54,64 96,22" fill="none" stroke="#22a64a" stroke-width="9" stroke-linejoin="round"/>
      <polygon points="86,10 118,2 110,34" fill="#22a64a"/>
    </svg>
    <p class="cta-band">Start savings now!. Packages available with no payments until 2025. Click to contact us!</p>
  </section>

  <section class="ad ad--wide" aria-label="Airwave Allies wide banner ad">
    <div class="ad-backdrop" role="img" aria-label="Deep blue background with faint stock-market candlestick chart"></div>
    <h1 class="headline">
      <span class="hl-line hl-build">Build</span>
      <span class="hl-line hl-budget">Your 2024 Budget</span>
      <span class="hl-with">with</span>
      <span class="hl-line hl-name">Airwave</span>
      <span class="hl-line hl-name-2">Allies</span>
    </h1>
    <div class="divider"></div>
    <h2 class="solutions-title">Solutions for Broadcasters</h2>
    <ul class="solutions">
      <li>Need to Improve Your Cash Flow?</li>
      <li>Need to Streamline Your Expenses?</li>
      <li>Need more Non-Traditional Revenue?</li>
    </ul>
    <div class="brand-corner">
      <svg viewBox="0 0 100 100" preserveAspectRatio="none" aria-hidden="true"><path d="M0 0H100V100C55 100 12 72 0 0Z" fill="#fff"/></svg>
      <p class="brand-name">Airwave<br>Allies</p>
    </div>
    <svg class="growth-chart" viewBox="0 0 130 140" aria-label="Rising bar chart with upward arrow">
      <defs>
        <linearGradient id="bar-fill-b" x1="0" y1="0" x2="0" y2="1"><stop offset="0" stop-color="#35b4ff"/><stop offset="1" stop-color="#1a8ae0"/></linearGradient>
      </defs>
      <rect x="2" y="100" width="20" height="38" fill="url(#bar-fill-b)"/>
      <rect x="28" y="86" width="20" height="52" fill="url(#bar-fill-b)"/>
      <rect x="54" y="72" width="20" height="66" fill="url(#bar-fill-b)"/>
      <rect x="80" y="56" width="20" height="82" fill="url(#bar-fill-b)"/>
      <rect x="106" y="40" width="20" height="98" fill="url(#bar-fill-b)"/>
      <polyline points="4,80 34,56 54,64 96,22" fill="none" stroke="#22a64a" stroke-width="9" stroke-linejoin="round"/>
      <polygon points="86,10 118,2 110,34" fill="#22a64a"/>
    </svg>
    <p class="cta-band">Start savings now!. Packages available with no payments until 2025. Click to contact us!</p>
  </section>

  <section class="ad ad--square" aria-label="Airwave Allies square ad">
    <div class="ad-backdrop" role="img" aria-label="Deep blue background with faint stock-market candlestick chart"></div>
    <h1 class="headline">
      <span class="hl-line hl-build">Build</span>
      <span class="hl-line hl-budget">Your 2024 Budget</span>
      <span class="hl-with">with</span>
      <span class="hl-line hl-name">Airwave</span>
      <span class="hl-line hl-name-2">Allies</span>
    </h1>
    <div class="divider"></div>
    <div class="brand-corner">
      <svg viewBox="0 0 100 100" preserveAspectRatio="none" aria-hidden="true"><path d="M0 0H100V100C55 100 12 72 0 0Z" fill="#fff"/></svg>
      <p class="brand-name">Airwave<br>Allies</p>
    </div>
    <svg class="growth-chart" viewBox="0 0 130 140" aria-label="Rising bar chart with upward arrow">
      <defs>
        <linearGradient id="bar-fill-c" x1="0" y1="0" x2="0" y2="1"><stop offset="0" stop-color="#35b4ff"/><stop offset="1" stop-color="#1a8ae0"/></linearGradient>
      </defs>
      <rect x="2" y="100" width="20" height="38" fill="url(#bar-fill-c)"/>
      <rect x="28" y="86" width="20" height="52" fill="url(#bar-fill-c)"/>
      <rect x="54" y="72" width="20" height="66" fill="url(#bar-fill-c)"/>
      <rect x="80" y="56" width="20" height="82" fill="url(#bar-fill-c)"/>
      <rect x="106" y="40" width="20" height="98" fill="url(#bar-fill-c)"/>
      <polyline points="4,80 34,56 54,64 96,22" fill="none" stroke="#22a64a" stroke-width="9" stroke-linejoin="round"/>
      <polygon points="86,10 118,2 110,34" fill="#22a64a"/>
    </svg>
    <h2 class="solutions-title">Solutions for Broadcasters</h2>
    <ul class="solutions">
      <li>Need to Improve Your Cash Flow?</li>
      <li>Need to Streamline Your Expenses?</li>
      <li>Need more Non-Traditional Revenue?</li>
    </ul>
  </section>

</main>
</body>
</html>
```